Hi everyone,
Fresh Walls Co is a business that renovates older houses into modern homes. I'm looking for a design that is clean and simple. It needs to show the client that renovating is a simple process. No more than 3 colours to be used thanks.

What I need:
1. Logo
2. Business card (one side)
3. Letter head (A4)

Looking forward to the designs!

Construction

Fresh Walls Co

Sans Serif

Must have
• Trading name: Fresh Walls Co
• Contact name: Declan Ashworth
• Email: declanashworth@freshwallsco.example.com.au
• Tel: 0412 758 204
• Clean and simple
Nice to have
• If design might include a few tools. eg Hammer, paint roller etc.
Should not have
• Complicated design

```html
<!DOCTYPE html>
<html lang="en">
<head>
<meta charset="utf-8">
<title>Fresh Walls Co – Stationery</title>
<link href="https://fonts.googleapis.com/css2?family=Roboto+Condensed:wght@400;700&family=Open+Sans:wght@400&display=swap" rel="stylesheet">
<style>
  :root {
    --board: #000000;
    --paper: #ffffff;
    --brand-red: #ec2229;
    --brand-grey: #58595b;
    --label: #ffffff;
  }
  * { margin: 0; padding: 0; box-sizing: border-box; }
  html, body { width: 1200px; height: 978px; overflow: hidden; background: var(--board); }
  .board { position: relative; width: 1200px; height: 978px; font-family: "Roboto Condensed", Arial, sans-serif; }

  .sheet { position: absolute; background: var(--paper); }
  .caption {
    position: absolute; font-family: "Open Sans", Arial, sans-serif; font-size: 10px;
    color: var(--label); text-align: center; letter-spacing: -0.2px;
  }

  .brand { position: absolute; display: flex; align-items: center; white-space: nowrap; }
  .brand-mark { background: var(--brand-red); flex: none; }
  .brand-name { font-weight: 700; color: var(--brand-red); line-height: 1; }

  /* Letterhead */
  .letterhead { left: 72px; top: 176px; width: 499px; height: 645px; }
  .letterhead .brand { left: 24px; top: 34px; gap: 8px; }
  .letterhead .brand-mark { width: 22px; height: 22px; }
  .letterhead .brand-name { font-size: 30px; }
  .letterhead-rule { position: absolute; left: 0; bottom: 36px; width: 100%; height: 4px; background: var(--brand-grey); }
  .letterhead-footer {
    position: absolute; left: 0; bottom: 0; width: 100%; height: 32px; background: var(--brand-red);
    display: flex; align-items: center; justify-content: center;
  }

  /* Logo panel */
  .logo-panel { left: 633px; top: 184px; width: 502px; height: 297px; }
  .logo-panel .brand { left: 0; right: 0; top: 0; bottom: 0; justify-content: center; gap: 14px; }
  .logo-panel .brand-mark { width: 40px; height: 40px; }
  .logo-panel .brand-name { font-size: 56px; }

  /* Business card */
  .business-card { left: 669px; top: 541px; width: 439px; height: 251px; overflow: hidden; }
  .business-card .brand { left: 0; right: 0; top: 44px; justify-content: center; gap: 9px; }
  .business-card .brand-mark { width: 24px; height: 24px; }
  .business-card .brand-name { font-size: 34px; }
  .card-name-band {
    position: absolute; left: 0; top: 136px; width: 100%; height: 31px; background: var(--brand-grey);
    color: var(--paper); font-weight: 700; font-size: 23px; letter-spacing: 0.3px;
    display: flex; align-items: center; justify-content: center; text-transform: uppercase;
  }
  .card-contact-band {
    position: absolute; left: 0; top: 167px; width: 100%; height: 84px; background: var(--brand-red);
    display: flex; justify-content: center; padding-top: 22px;
  }

  .contact-line { display: flex; align-items: center; gap: 7px; color: var(--paper); font-size: 12px; white-space: nowrap; }
  .business-card .contact-line { font-size: 12px; gap: 6px; }
  .contact-line svg { flex: none; }
  .contact-gap { width: 6px; }
</style>
</head>
<body>
<div class="board">

  <section class="sheet letterhead" aria-label="Letterhead">
    <div class="brand"><span class="brand-mark"></span><span class="brand-name">Fresh Walls Co</span></div>
    <div class="letterhead-rule"></div>
    <footer class="letterhead-footer">
      <div class="contact-line">
        <span>declanashworth@freshwallsco.example.com.au</span>
        <svg width="22" height="13" viewBox="0 0 22 13" aria-hidden="true"><rect width="22" height="13" fill="#fff"/><path d="M0 0 L11 7 L22 0 M0 13 L8 5.5 M22 13 L14 5.5" stroke="#ec2229" stroke-width="1.2" fill="none"/></svg>
        <span class="contact-gap"></span>
        <span>0412 758 204</span>
        <svg width="8" height="14" viewBox="0 0 8 14" aria-hidden="true"><path d="M1 1 C5 1 8 5 7 9 C6.5 12 4 13 2 13 L1.5 11 C3 11 4.5 10 4.5 8 C4.8 6 3.5 3.5 1.5 3.2 Z" fill="#fff"/></svg>
      </div>
    </footer>
  </section>
  <div class="caption" style="left:72px;width:499px;top:835px;">LETTER HEAD</div>

  <section class="sheet logo-panel" aria-label="Logo">
    <div class="brand"><span class="brand-mark"></span><span class="brand-name">Fresh Walls Co</span></div>
  </section>
  <div class="caption" style="left:633px;width:502px;top:498px;">LOGO</div>

  <section class="sheet business-card" aria-label="Business card">
    <div class="brand"><span class="brand-mark"></span><span class="brand-name">Fresh Walls Co</span></div>
    <div class="card-name-band">Declan Ashworth</div>
    <div class="card-contact-band">
      <div class="contact-line">
        <span>declanashworth@freshwallsco.example.com.au</span>
        <svg width="22" height="13" viewBox="0 0 22 13" aria-hidden="true"><rect width="22" height="13" fill="#fff"/><path d="M0 0 L11 7 L22 0 M0 13 L8 5.5 M22 13 L14 5.5" stroke="#ec2229" stroke-width="1.2" fill="none"/></svg>
        <span class="contact-gap"></span>
        <span>0412 758 204</span>
        <svg width="8" height="14" viewBox="0 0 8 14" aria-hidden="true"><path d="M1 1 C5 1 8 5 7 9 C6.5 12 4 13 2 13 L1.5 11 C3 11 4.5 10 4.5 8 C4.8 6 3.5 3.5 1.5 3.2 Z" fill="#fff"/></svg>
      </div>
    </div>
  </section>
  <div class="caption" style="left:669px;width:439px;top:814px;">BUSINESS CARD</div>

</div>
</body>
</html>
```